4th Generation Family Business Needs a New Card Design!

We are a family owned 4th Generation company. We are based in the Sydney, Australia area and we are desperately in need of a more modern and classy card. We are monumental masons who design, supply & erect lasting memorials throughout cemeteries in Sydney. Our customers are normally in a period of grieving. I have attached logo files that will need to be implemented on the card. Company was established 1935. Australian Owned and Operated. Card needs to be designed to PIXO.com specification.

Target Market(s)

Our target market is based upon people that a grieving for family members that have passed away. We also deal with alot of companies that own and operate cemeteries.

Industry/Entity Type

Business

Contact Information for Business Card

Simon Harcourt, Operations Manager, 0417293086, simon@harcourtmemorials.com.au
Lewis Harcourt, Director, 0491630572, lewis@harcourtmemorials.com.au
Phone # 02 9561 3048
Website: www.harcourtmemorials.com.au
Address: Suite 17, 8 Palfrey Lane, West Carlow, Sydney NSW 2156

Font styles to use
Serif
Decorative
Script

Requirements
Must have
• Would like to see the logo nicely implemented with a modern design. Embossed lettering would be a nice additive.

```html
<!DOCTYPE html>
<html lang="en">
<head>
<meta charset="utf-8">
<title>Harcourt Memorials – Business Card</title>
<link rel="stylesheet" href="https://fonts.googleapis.com/css2?family=Lato:wght@400;700&display=swap">
<style>
  :root {
    --backdrop: #e7e4df;
    --card-light: #ffffff;
    --card-dark: #262626;
    --gold: #e6b62a;
    --ink: #1e1e1e;
    --grey: #7b7b7b;
    --rule: #b9b9b9;
    --white: #ffffff;
  }
  * { margin: 0; padding: 0; box-sizing: border-box; }
  html, body { width: 1200px; height: 960px; overflow: hidden; }
  body {
    position: relative;
    background: var(--backdrop);
    font-family: "Lato", Arial, sans-serif;
  }
  .card {
    position: absolute;
    left: 257px;
    width: 703px;
    height: 400px;
    box-shadow: 0 3px 10px rgba(0,0,0,0.18);
    overflow: hidden;
  }
  .card--front { top: 52px; background: var(--card-light); }
  .card--back  { top: 508px; background: var(--card-dark); }

  .wordmark {
    position: absolute;
    text-align: center;
    font-family: "Lato", Arial, sans-serif;
    font-weight: 400;
    line-height: 1;
  }
  .wordmark__name { display: block; letter-spacing: 1px; }
  .wordmark__sub  { display: block; letter-spacing: 3px; margin-top: 8px; }

  .card--front .wordmark { left: 63px; width: 260px; top: 170px; color: var(--ink); }
  .card--front .wordmark__name { font-size: 44px; }
  .card--front .wordmark__sub  { font-size: 20px; }

  .card--back .wordmark { left: 201px; width: 300px; top: 135px; color: var(--white); }
  .card--back .wordmark__name { font-size: 50px; }
  .card--back .wordmark__sub  { font-size: 23px; }

  .person { position: absolute; left: 370px; top: 90px; }
  .person__name { font-size: 24px; font-weight: 700; color: var(--gold); letter-spacing: 0.5px; line-height: 1.1; }
  .person__role { font-size: 18px; color: var(--grey); letter-spacing: 0.8px; margin-top: 1px; }

  .contact-row {
    position: absolute;
    left: 370px;
    display: flex;
    align-items: center;
    font-size: 16px;
    color: var(--grey);
    line-height: 1;
  }
  .contact-row .icon { width: 14px; height: 14px; margin-right: 9px; flex: none; }
  .row-mobile { top: 151px; }
  .row-email  { top: 174px; }
  .row-phone  { top: 290px; }
  .row-web    { top: 313px; }

  .divider { position: absolute; left: 370px; right: 0; top: 202px; height: 1px; background: var(--rule); }

  .office { position: absolute; left: 371px; top: 213px; color: var(--grey); font-size: 16px; line-height: 23px; }
  .office__name { color: var(--gold); font-weight: 700; }

  .back-url {
    position: absolute;
    left: 0; right: 0; top: 326px;
    text-align: center;
    font-size: 15px;
    letter-spacing: 2.6px;
    color: var(--white);
  }
  .back-url .accent { color: var(--gold); }
</style>
</head>
<body>

<section class="card card--front">
  <div class="wordmark">
    <span class="wordmark__name">HARCOURT</span>
    <span class="wordmark__sub">MEMORIALS</span>
  </div>

  <div class="person">
    <div class="person__name">Lewis Harcourt</div>
    <div class="person__role">Director</div>
  </div>

  <div class="contact-row row-mobile">
    <svg class="icon" viewBox="0 0 14 14" aria-hidden="true"><rect x="3.5" y="1" width="7" height="12" rx="1.2" fill="none" stroke="var(--gold)" stroke-width="1.4"/><line x1="6" y1="11" x2="8" y2="11" stroke="var(--gold)" stroke-width="1.2"/></svg>
    <span>0491630572</span>
  </div>
  <div class="contact-row row-email">
    <svg class="icon" viewBox="0 0 14 14" aria-hidden="true"><rect x="1" y="3" width="12" height="8" fill="none" stroke="var(--gold)" stroke-width="1.4"/><polyline points="1,3 7,8 13,3" fill="none" stroke="var(--gold)" stroke-width="1.4"/></svg>
    <span>lewis@harcourtmemorials.com.au</span>
  </div>

  <div class="divider"></div>

  <div class="office">
    <div class="office__name">Harcourt Memorials</div>
    <div>Suite 17, 8 Palfrey Lane</div>
    <div>West Carlow, Sydney NSW 2156</div>
  </div>

  <div class="contact-row row-phone">
    <svg class="icon" viewBox="0 0 14 14" aria-hidden="true"><path d="M4 1.5 L6 4 L4.8 5.6 Q6 8.6 8.6 9.6 L10 8.4 L12.5 10.4 L11 12.5 Q5 12 2.2 4 Z" fill="var(--gold)"/></svg>
    <span>02 9561 3048</span>
  </div>
  <div class="contact-row row-web">
    <svg class="icon" viewBox="0 0 14 14" aria-hidden="true"><circle cx="7" cy="7" r="5.8" fill="none" stroke="var(--gold)" stroke-width="1.2"/><ellipse cx="7" cy="7" rx="2.6" ry="5.8" fill="none" stroke="var(--gold)" stroke-width="1"/><line x1="1.2" y1="7" x2="12.8" y2="7" stroke="var(--gold)" stroke-width="1"/></svg>
    <span>www.harcourtmemorials.com.au</span>
  </div>
</section>

<section class="card card--back">
  <div class="wordmark">
    <span class="wordmark__name">HARCOURT</span>
    <span class="wordmark__sub">MEMORIALS</span>
  </div>
  <div class="back-url">www.<span class="accent">harcourtmemorials</span>.com.au</div>
</section>

</body>
</html>
```